Boutique Store Selling Antiques and Unique Finds

I need a Web Page designed for my Store Called "Willow Lane". I would like a very classic, muted design that looks European when pulled up. I will be selling Antiques from all over the world and Unique finds that have reproduced. I will also be selling high-end purses and jewelry with unique, reasonable products for the every-day buyer as well.

Target Market(s)

25-70 year old men and women;)

Coding

Coded - Design and coding required

Number of Pages Required

1 page

Colors

Designer to choose only greyscale colors for use in the design.

Requirements
Must have
• I want it

```html
<!DOCTYPE html>
<html lang="en">
<head>
<meta charset="utf-8">
<title>Willow Lane — Antiques &amp; Unique Finds</title>
<link href="https://fonts.googleapis.com/css2?family=Cinzel:wght@400;500&family=Roboto:wght@400;500;700&display=swap" rel="stylesheet">
<style>
:root{
  --page:#f1f1f1;
  --panel:#f6f6f6;
  --white:#ffffff;
  --ink:#111111;
  --text:#2b2b2b;
  --muted:#777777;
  --line:#dddddd;
  --footer:#333333;
  --footer-text:#f0f0f0;
  --photo-light:#cfcac3;
  --photo-mid:#8f877c;
  --photo-dark:#4a4036;
}
*{box-sizing:border-box;margin:0;padding:0}
html,body{width:1200px;height:2750px;overflow:hidden}
body{background:var(--page);font-family:'Roboto',Arial,sans-serif;color:var(--text);position:relative}
.abs{position:absolute}

.hero{left:0;top:75px;width:1200px;height:557px;background:radial-gradient(ellipse at 50% 60%,#8a7558 0%,#6e5d47 28%,#c9c2b8 55%,#e4e0da 100%)}
.header{left:77px;top:0;width:1045px;height:140px;background:var(--panel)}
.search{left:35px;top:24px;width:243px;height:34px;border-bottom:1px solid var(--line);font-size:14px;color:var(--muted);padding:14px 8px 0}
.search svg{position:absolute;right:12px;top:12px}
.brand{left:0;width:1045px;top:18px;text-align:center}
.brand .mark{width:28px;height:28px;border-radius:50%;background:var(--ink);margin:0 auto 6px}
.brand .name{font-family:'Cinzel',serif;font-size:20px;letter-spacing:3px;color:var(--ink)}
.account{right:34px;top:37px;font-size:13.5px;font-weight:500;color:#555;display:flex;gap:18px;align-items:center;letter-spacing:.3px}
.account .sep{width:1px;height:14px;background:#aaa}
.account span{display:flex;align-items:center;gap:6px}
.nav{left:0;top:101px;width:1045px;display:flex;justify-content:center;gap:25px;font-size:13.5px;font-weight:500;color:var(--ink);letter-spacing:.4px}

.categories{left:111px;top:742px;width:978px;height:370px;background:var(--panel);border:1px solid #e6e6e6;display:flex}
.cat-group{flex:1;border-right:1px solid #e6e6e6;padding:0 7px}
.cat-group:last-child{border-right:none}
.cat-group h3{font-size:14.5px;font-weight:500;letter-spacing:.6px;text-align:center;color:var(--ink);height:77px;line-height:77px}
.tiles{display:flex;gap:7px}
.tile{width:232px;height:281px;position:relative;border-radius:3px;overflow:hidden}
.tile .label{position:absolute;left:0;bottom:0;width:100%;height:50px;background:rgba(40,40,40,.55);color:#fff;font-weight:700;font-size:15.5px;letter-spacing:.6px;text-align:center;line-height:50px}
.t1{background:linear-gradient(160deg,#b8b3ab,#6b5442 70%,#3e3029)}
.t2{background:linear-gradient(160deg,#9a968f,#cfcbc4 45%,#5c5850)}
.t3{background:linear-gradient(160deg,#4b3c31,#7a6350 50%,#2e241e)}
.t4{background:linear-gradient(180deg,#d8d2c6,#5a4b36 50%,#6a6660)}

.newsletter{left:0;top:1215px;width:1200px;height:408px;background:linear-gradient(180deg,#e6e6e6,#efefef)}
.newsletter h2{position:absolute;top:58px;width:100%;text-align:center;font-family:'Cinzel',serif;font-weight:400;font-size:35px;letter-spacing:2.5px;line-height:40px;color:var(--ink)}
.field{top:175px;width:291px;height:47px;background:var(--white);border:1px solid var(--line);border-radius:2px;font-size:14.5px;color:#666;padding:15px 18px}
.interests{left:303px;top:246px;display:flex;align-items:center;font-size:11.5px;color:#555}
.interests b{font-weight:500;font-size:12.5px;color:#444;margin-right:30px;letter-spacing:.3px}
.check{display:flex;align-items:center;gap:10px;margin-right:32px}
.check i{width:13px;height:13px;border:1px solid #ccc;background:#fff;border-radius:2px}
.subscribe{left:534px;top:293px;width:132px;height:46px;background:var(--ink);color:#fff;font-weight:700;font-size:15px;letter-spacing:.5px;text-align:center;line-height:46px;border-radius:2px}

.shop-title{top:1700px;width:1200px;text-align:center;font-family:'Cinzel',serif;font-size:35px;letter-spacing:2.5px;color:var(--ink)}
.product{top:1782px;width:485px;text-align:center}
.product .photo{height:428px}
.p1 .photo{background:linear-gradient(180deg,#d2cdc4 0%,#8a7150 45%,#3c3027 75%,#5a2a22 100%)}
.p2 .photo{background:linear-gradient(135deg,#4a3326,#8a5d35 45%,#c8b79a 70%,#5b3a24)}
.product h4{margin-top:28px;font-size:16px;font-weight:500;letter-spacing:.8px;color:var(--ink)}
.product .price{margin-top:10px;font-size:32px;font-weight:500;letter-spacing:1px;color:var(--ink)}

.footer{left:0;top:2416px;width:1200px;height:334px;background:var(--footer);color:var(--footer-text)}
.footer h5{font-size:14px;font-weight:700;text-decoration:underline;text-underline-offset:3px;margin-bottom:22px}
.col{top:48px}
.about p{width:260px;font-size:14.5px;line-height:30px;text-align:justify}
.about .more{margin-top:18px;font-size:14px;font-weight:700;text-decoration:underline;text-underline-offset:3px}
.links li{list-style:none;font-size:14px;height:34px;display:flex;align-items:center;gap:14px}
.contact .row{display:flex;align-items:center;gap:18px;font-size:14px;line-height:22px;margin-bottom:18px}
.contact .ic{width:29px;height:29px;border-radius:50%;background:#fff;display:flex;align-items:center;justify-content:center;flex:none}
.divider{left:111px;top:272px;width:978px;height:1px;background:#888}
.copyright{left:121px;top:296px;font-size:14.5px}
.social{left:958px;top:287px;display:flex;gap:11px}
.social i{width:36px;height:36px;border:2px solid #fff;border-radius:50%}
</style>
</head>
<body>

<div class="abs hero" role="img" aria-label="Antique gilded crown with blue and clear stones"></div>

<header class="abs header">
  <div class="abs search">Search
    <svg width="13" height="13" viewBox="0 0 14 14"><circle cx="6" cy="6" r="4.5" fill="none" stroke="#666" stroke-width="1.6"/><line x1="9.3" y1="9.3" x2="13" y2="13" stroke="#666" stroke-width="1.6"/></svg>
  </div>
  <div class="abs brand"><div class="mark"></div><div class="name">Willow Lane</div></div>
  <div class="abs account">
    <span><svg width="11" height="12" viewBox="0 0 11 12"><circle cx="5.5" cy="3" r="3" fill="#666"/><path d="M0 12c0-4 2.5-5.5 5.5-5.5S11 8 11 12z" fill="#666"/></svg>LOG IN / REGISTER</span>
    <i class="sep"></i>
    <span><svg width="13" height="12" viewBox="0 0 13 12"><path d="M0 1h2.5l2 7h7l1.5-5H4" fill="none" stroke="#666" stroke-width="1.6"/><circle cx="5" cy="10.5" r="1.2" fill="#666"/><circle cx="10.5" cy="10.5" r="1.2" fill="#666"/></svg>0 ITEMS</span>
  </div>
  <nav class="abs nav">
    <span>HOME</span><span>SHOP ONLINE</span><span>NEW ARRIVALS</span><span>ANTIQUES &amp; UNIQUE FINDS</span><span>JEWELS</span><span>HIGH-END PURSES</span><span>EVENTS</span><span>CONTACT US</span>
  </nav>
</header>

<section class="abs categories">
  <div class="cat-group">
    <h3>ANTIQUES AND UNIQUE FINDS</h3>
    <div class="tiles">
      <div class="tile t1" role="img" aria-label="Gramophone, radio and antique furniture"><div class="label">ANTIQUES</div></div>
      <div class="tile t2" role="img" aria-label="Silver teapots and tableware"><div class="label">UNIQUE FINDS</div></div>
    </div>
  </div>
  <div class="cat-group">
    <h3>HIGH-END PURSES &amp; JEWELRY WITH UNIQUE</h3>
    <div class="tiles">
      <div class="tile t3" role="img" aria-label="Brown leather bag"><div class="label">HIGH-END PURSES</div></div>
      <div class="tile t4" role="img" aria-label="Jewelled antique crown"><div class="label">JEWELRY</div></div>
    </div>
  </div>
</section>

<section class="abs newsletter">
  <h2>SIGN UP TO OUR NEWSLETTER<br>TO STAY UP TO DATE</h2>
  <div class="abs field" style="left:303px">Your Name</div>
  <div class="abs field" style="left:606px">Email Address</div>
  <div class="abs interests">
    <b>SELECT ADDITIONAL INTERESTS</b>
    <span class="check"><i></i>Antiques</span>
    <span class="check"><i></i>Unique</span>
    <span class="check"><i></i>Purses</span>
    <span class="check"><i></i>Jewelry</span>
  </div>
  <div class="abs subscribe">SUBSCRIBE</div>
</section>

<h2 class="abs shop-title">SHOP ONLINE</h2>
<div class="abs product p1" style="left:111px">
  <div class="photo" role="img" aria-label="Gilded crown resting on old leather books"></div>
  <h4>PRODUCT TITLE</h4><div class="price">£275.00</div>
</div>
<div class="abs product p2" style="left:602px">
  <div class="photo" role="img" aria-label="Antique cabinets, vases and porcelain display"></div>
  <h4>PRODUCT TITLE</h4><div class="price">£275.00</div>
</div>

<footer class="abs footer">
  <div class="abs col about" style="left:123px">
    <h5>ABOUT US</h5>
    <p>Lorem ipsum dolor sit amet, consectetur adipiscing elit, sed do eiusmod tempor incididunt ut labore et dolore magna aliquaUt enim ad minim.</p>
    <div class="more">READ MORE »</div>
  </div>
  <div class="abs col" style="left:462px">
    <h5>QUICK LINKS</h5>
    <ul class="links"><li>»<span>Home</span></li><li>»<span>About Us</span></li><li>»<span>Our Products</span></li><li>»<span>Shop Online</span></li><li>»<span>Contact Us</span></li></ul>
  </div>
  <div class="abs col" style="left:660px">
    <h5>OTHER LINKS</h5>
    <ul class="links"><li>»<span>FAQ</span></li><li>»<span>Help Service</span></li><li>»<span>Terms Of Use</span></li><li>»<span>Privacy Policy</span></li><li>»<span>Blog</span></li></ul>
  </div>
  <div class="abs col contact" style="left:868px">
    <h5>CONTACT US</h5>
    <div class="row"><span class="ic"><svg width="12" height="15" viewBox="0 0 12 15"><path d="M6 0a6 6 0 0 0-6 6c0 4 6 9 6 9s6-5 6-9a6 6 0 0 0-6-6z" fill="#333"/><circle cx="6" cy="6" r="2.2" fill="#fff"/></svg></span><span>214 , Harrow Row Close<br>United States</span></div>
    <div class="row"><span class="ic"><svg width="14" height="14" viewBox="0 0 14 14"><path d="M3 0l2.5 3.5-1.6 1.8a8 8 0 0 0 4.8 4.8l1.8-1.6L14 11l-2 3C5.5 14 0 8.5 0 2z" fill="#333"/></svg></span><span>1 555 014 2290</span></div>
    <div class="row"><span class="ic"><svg width="14" height="11" viewBox="0 0 14 11"><rect x="1" y="1" width="12" height="9" rx="1" fill="none" stroke="#333" stroke-width="1.5"/><path d="M1 1.5l6 4.5 6-4.5" fill="none" stroke="#333" stroke-width="1.5"/></svg></span><span>info@willowlane.com</span></div>
  </div>
  <div class="abs divider"></div>
  <div class="abs copyright">© 2021 Willow Lane. All Rights Reserved</div>
  <div class="abs social"><i></i><i></i><i></i></div>
</footer>

</body>
</html>
```